Machining Business Order Thank You Insert

I am looking for a business style card to include with orders that I ship. The card needs to thank the recipient for their order, and encourage them to leave a review. The card should include my business name and contact information and have an area to hand write a message.

I mainly sale on Craftlane and my own website. We are a machining an manufacturing business that are in the sale of mostly metal machined and 3d printed plastic products.

The front of the card should include the following:
Logo: (attached)
Snapgram: https://www.snapgram.example/kelvomill/
Friendsbook: https://www.friendsbook.example/KelvoMill
Website: https://www.kelvomill.example/

The back of the card needs an area to write a message

Industry/Entity Type

3D Printing, Machining, Craftlane

Contact Information for Business Card

Black or white front, white back to write a personal message

Font styles to use
Sans Serif

Colors

Designer to choose colors to be used in the design.

Requirements
Must have
• Encourage a review, social media info

```html
<!DOCTYPE html>
<html lang="en">
<head>
<meta charset="utf-8">
<title>KelvoMill – Order Thank You Insert</title>
<link rel="stylesheet" href="https://fonts.googleapis.com/css2?family=Lato:wght@400;700;900&display=swap">
<style>
  :root {
    --stage: #9b9b9b;
    --paper: #ffffff;
    --pattern-tone: #f1f1f1;
    --brand-orange: #f05a28;
    --brand-grey: #6d6e70;
    --ink-light: #ffffff;
  }
  html, body {
    margin: 0;
    padding: 0;
    width: 1200px;
    height: 1200px;
    overflow: hidden;
    background: var(--stage);
  }
  .canvas {
    position: relative;
    width: 1200px;
    height: 1200px;
  }
  .card {
    position: absolute;
    top: 303px;
    width: 365px;
    height: 594px;
    background: var(--paper);
    overflow: hidden;
  }
  .card--back { left: 201px; }
  .card--front { left: 600px; }
  .card__message-area {
    width: 100%;
    height: 100%;
    background: linear-gradient(180deg, var(--paper) 0%, var(--pattern-tone) 50%, var(--paper) 100%);
  }
  .card__art { display: block; width: 100%; height: 100%; }
  .headline {
    font-family: "Lato", sans-serif;
    font-weight: 900;
    fill: var(--ink-light);
  }
  .headline--main { font-size: 84px; }
  .headline--sub { font-size: 58px; font-weight: 700; }
  .review-prompt {
    font-family: "Lato", sans-serif;
    font-weight: 700;
    font-size: 27px;
    fill: var(--brand-orange);
  }
  .brand-name {
    font-family: "Lato", sans-serif;
    font-weight: 700;
    font-size: 36px;
    letter-spacing: 10px;
    fill: var(--brand-grey);
  }
  .contact-line {
    font-family: "Lato", sans-serif;
    font-size: 27px;
    fill: var(--ink-light);
  }
  .contact-icon { fill: var(--ink-light); }
</style>
</head>
<body>
<main class="canvas">
  <section class="card card--back">
    <div class="card__message-area" role="img" aria-label="Faint repeating geometric background pattern behind space for a handwritten message"></div>
  </section>

  <section class="card card--front">
    <svg class="card__art" viewBox="0 0 587 955" preserveAspectRatio="none" xmlns="http://www.w3.org/2000/svg">
      <rect class="band band--top" x="0" y="0" width="587" height="400" fill="var(--brand-orange)"/>
      <rect class="band band--bottom" x="0" y="540" width="587" height="415" fill="var(--brand-grey)"/>
      <polygon class="band band--middle" points="0,362 292,285 587,378 587,580 292,657 0,566" fill="var(--paper)"/>

      <text class="headline headline--main" x="293" y="140" text-anchor="middle">Thank you!</text>
      <text class="headline headline--sub" x="293" y="240" text-anchor="middle">for your order</text>

      <text class="review-prompt" x="293" y="425" text-anchor="middle">Loved your order?</text>
      <text class="review-prompt" x="293" y="462" text-anchor="middle">Please leave us a review!</text>

      <text class="brand-name" x="298" y="574" text-anchor="middle">KELVOMILL</text>

      <g class="contact-icons">
        <circle class="contact-icon" cx="252" cy="744" r="16"/>
        <circle class="contact-icon" cx="294" cy="744" r="16"/>
        <circle class="contact-icon" cx="335" cy="744" r="16"/>
      </g>

      <text class="contact-line" x="293" y="803" text-anchor="middle">www.kelvomill.example</text>
      <text class="contact-line" x="293" y="843" text-anchor="middle">www.snapgram.example/kelvomill</text>
      <text class="contact-line" x="293" y="882" text-anchor="middle">www.friendsbook.example/KelvoMill</text>
    </svg>
  </section>
</main>
</body>
</html>
```